Business Card design which attached logo. Company is called Crestline Shield and main colours are Orange & Black.

Company specialises in Paint Protection and Detailing for supercars.

Details needed on business card:

Sales

Address: Unit 14, 517 Hadley Road, Fernvale Heights, NSW 2200

Phone: 02 6194 2738

website: www.crestlineshield.com.au

Email: sales@crestlineshield.com.au

```html
<!DOCTYPE html>
<html lang="en">
<head>
<meta charset="utf-8">
<title>Crestline Shield – Business Card</title>
<link rel="stylesheet" href="https://fonts.googleapis.com/css2?family=Lato:wght@300;400&display=swap">
<style>
  :root {
    --backdrop: #26282c;
    --card-black: #070809;
    --orange: #f05a22;
    --orange-soft: #d9531f;
    --ink-light: #e4e4e4;
    --rule: #5a5c60;
  }
  * { box-sizing: border-box; margin: 0; padding: 0; }
  html, body { width: 1200px; height: 900px; overflow: hidden; }
  body {
    background: var(--backdrop);
    font-family: "Lato", sans-serif;
    display: flex;
    align-items: center;
    justify-content: center;
    gap: 40px;
  }
  .card {
    width: 540px;
    height: 309px;
    background: var(--card-black);
    position: relative;
    overflow: hidden;
    box-shadow: 0 14px 30px rgba(0,0,0,.45);
  }

  /* Front */
  .card-front .brand {
    position: absolute;
    left: 44px;
    top: 70px;
    width: 200px;
    display: flex;
    align-items: center;
    gap: 10px;
  }
  .brand-dot {
    width: 10px; height: 10px;
    border-radius: 50%;
    background: var(--orange);
    flex: none;
  }
  .brand-name {
    color: var(--orange);
    font-weight: 300;
    text-transform: uppercase;
    letter-spacing: .06em;
    font-size: 19px;
    white-space: nowrap;
  }
  .divider {
    position: absolute;
    left: 262px;
    top: 54px;
    width: 1px;
    height: 150px;
    background: var(--rule);
  }
  .contact {
    position: absolute;
    left: 282px;
    top: 58px;
  }
  .contact-name {
    color: var(--ink-light);
    font-weight: 300;
    font-size: 24px;
    letter-spacing: .08em;
    text-transform: uppercase;
    margin-bottom: 16px;
  }
  .contact-list { list-style: none; }
  .contact-list li {
    display: flex;
    align-items: center;
    gap: 9px;
    color: var(--orange);
    font-size: 14.5px;
    font-weight: 400;
    line-height: 26px;
  }
  .contact-list svg { width: 14px; height: 14px; flex: none; }
  .address-band {
    position: absolute;
    left: 0; right: 0; bottom: 0;
    height: 30px;
    background: var(--orange);
    color: var(--card-black);
    font-size: 14px;
    display: flex;
    align-items: center;
    padding-left: 44px;
    letter-spacing: .01em;
  }

  /* Back */
  .card-back {
    display: flex;
    align-items: center;
    justify-content: center;
  }
  .card-back .brand-name { font-size: 30px; }
  .card-back .brand { display: flex; align-items: center; gap: 14px; }
  .card-back .brand-dot { width: 14px; height: 14px; }
</style>
</head>
<body>
  <section class="card card-front" aria-label="Business card front">
    <div class="brand">
      <span class="brand-dot"></span>
      <span class="brand-name">Crestline Shield</span>
    </div>
    <div class="divider"></div>
    <div class="contact">
      <p class="contact-name">Liam Carter</p>
      <ul class="contact-list">
        <li>
          <svg viewBox="0 0 16 16" aria-hidden="true"><path fill="#fff" d="M4 1.5l2.2 3-1.3 1.6c.8 1.8 2.2 3.2 4 4l1.6-1.3 3 2.2-1.3 2.5C7 13.5 2.5 9 1.5 3.8z"/></svg>
          02 6194 2738
        </li>
        <li>
          <svg viewBox="0 0 16 16" aria-hidden="true"><rect x="1.5" y="3.5" width="13" height="9" fill="#fff"/><path d="M1.5 3.5l6.5 5 6.5-5" fill="none" stroke="#070809" stroke-width="1.2"/></svg>
          sales@crestlineshield.com.au
        </li>
        <li>
          <svg viewBox="0 0 16 16" aria-hidden="true"><g fill="none" stroke="#fff" stroke-width="1.2"><circle cx="8" cy="8" r="6.3"/><ellipse cx="8" cy="8" rx="2.8" ry="6.3"/><path d="M1.7 8h12.6M2.8 4.8h10.4M2.8 11.2h10.4"/></g></svg>
          www.crestlineshield.com.au
        </li>
      </ul>
    </div>
    <div class="address-band">Unit 14, 517 Hadley Road, Fernvale Heights, NSW 2200</div>
  </section>

  <section class="card card-back" aria-label="Business card back">
    <div class="brand">
      <span class="brand-dot"></span>
      <span class="brand-name">Crestline Shield</span>
    </div>
  </section>
</body>
</html>
```